Northfield Builders Guild Business card

We are looking for a new business card design with photo included.
Our business is a nonprofit construction contractor membership organization. We offer business education, assist with business setup and licensing, provide safety training, and provide a member directory.
URL: www.builderslinkguild.org
Color code:
CMYK: 0 cyan, 42 magenta, 100 yellow, 0 black for Print.
Hexidecimal: #FF9900
RGB: R 255; G 153; B 0

```html
<!DOCTYPE html>
<html lang="en">
<head>
<meta charset="utf-8">
<title>Northfield Builders Guild – Business Card</title>
<link rel="stylesheet" href="https://fonts.googleapis.com/css2?family=Montserrat:wght@700;800&family=Arimo:wght@400&display=swap">
<style>
  :root {
    --orange: #ff9900;
    --charcoal: #333333;
    --ink: #2b2b2b;
    --white: #ffffff;
    --backdrop: #262626;
  }
  * { margin: 0; padding: 0; box-sizing: border-box; }
  html, body { width: 1200px; height: 1015px; overflow: hidden; }
  body {
    background: var(--backdrop);
    position: relative;
    font-family: "Arimo", Arial, sans-serif;
  }
  .card {
    position: absolute;
    width: 620px;
    height: 354px;
    box-shadow: 0 14px 30px rgba(0,0,0,.45);
  }
  .card--front { left: 110px; top: 100px; background: var(--orange); }
  .card--back  { left: 470px; top: 560px; background: var(--charcoal); }

  .wordmark {
    font-family: "Montserrat", Arial, sans-serif;
    font-weight: 800;
    text-transform: uppercase;
    line-height: 1.02;
    letter-spacing: -0.5px;
  }
  .card--front .wordmark {
    position: absolute; left: 0; right: 0; top: 92px;
    text-align: center; font-size: 46px; color: var(--ink);
  }
  .card--front .site {
    position: absolute; left: 0; right: 0; top: 262px;
    text-align: center; font-size: 15px; letter-spacing: 2px; color: var(--ink);
  }
  .card--back .wordmark {
    position: absolute; right: 36px; top: 34px;
    text-align: right; font-size: 30px; color: var(--white);
  }
  .holder {
    position: absolute; left: 40px; top: 168px;
    font-family: "Montserrat", Arial, sans-serif; font-weight: 800; text-transform: uppercase;
  }
  .holder__name { color: var(--orange); font-size: 22px; }
  .holder__role { color: var(--white); font-size: 13px; margin-top: 2px; }
  .contacts { position: absolute; left: 40px; top: 232px; list-style: none; }
  .contacts li {
    display: flex; align-items: center; gap: 8px;
    color: var(--white); font-size: 14px; height: 24px;
  }
  .contacts .note { color: var(--orange); }
  .contacts svg { width: 19px; height: 19px; flex: none; }
  .address {
    position: absolute; left: 350px; top: 190px;
    color: var(--white); font-size: 14px; line-height: 1.35;
  }
  .address .site { color: var(--orange); display: block; margin-top: 10px; }
</style>
</head>
<body>
  <section class="card card--front">
    <div class="wordmark">Northfield<br>Builders Guild</div>
    <div class="site">www.builderslinkguild.org</div>
  </section>

  <section class="card card--back">
    <div class="wordmark">Northfield<br>Builders Guild</div>
    <div class="holder">
      <div class="holder__name">Daniel Harper</div>
      <div class="holder__role">Managing Director</div>
    </div>
    <ul class="contacts">
      <li>
        <svg viewBox="0 0 20 20" aria-hidden="true"><circle cx="10" cy="10" r="10" fill="var(--orange)"/><path d="M7 5.5l1.6 2.4-1 1c.6 1.3 1.6 2.3 2.9 2.9l1-1 2.4 1.6-.9 1.6C9.5 13.8 6.2 10.5 5.4 6.4z" fill="var(--charcoal)"/></svg>
        <span>(541) 555-0142 <span class="note">(Office)</span></span>
      </li>
      <li>
        <svg viewBox="0 0 20 20" aria-hidden="true"><circle cx="10" cy="10" r="10" fill="var(--orange)"/><rect x="7" y="4.5" width="6" height="11" rx="1" fill="none" stroke="var(--charcoal)" stroke-width="1.4"/></svg>
        <span>800-555-0178</span>
      </li>
      <li>
        <svg viewBox="0 0 20 20" aria-hidden="true"><circle cx="10" cy="10" r="10" fill="var(--orange)"/><rect x="7" y="5" width="6" height="3" fill="var(--charcoal)"/><rect x="5" y="8.5" width="10" height="5" rx="1" fill="var(--charcoal)"/><rect x="7" y="12" width="6" height="3" fill="var(--charcoal)"/></svg>
        <span>503.555.0193</span>
      </li>
      <li>
        <svg viewBox="0 0 20 20" aria-hidden="true"><circle cx="10" cy="10" r="10" fill="var(--orange)"/><rect x="5" y="6.5" width="10" height="7" fill="var(--charcoal)"/><path d="M5 6.5l5 4 5-4" fill="none" stroke="var(--orange)" stroke-width="1"/></svg>
        <span>info@nbguild.org</span>
      </li>
    </ul>
    <address class="address">
      2450 Cedar Mill Ave<br>
      Suite #210, Portland<br>
      OR 97201
      <span class="site">www.builderslinkguild.org</span>
    </address>
  </section>
</body>
</html>
```